Business card design for Virtual Assistance company

I need a business card designed for my virtual assistance company. We are a small company who services primarily C-level executive clients. The card needs to be double sided with the following contact information on the back:
Melissa Thornbury
Owner/CEO
info@rkpadvisory.net
www.rkpadvisory.net
555.302.9817

The front side should just have the company name incorporated: "RKP Advisory" and "virtual assistance"

The card should be simplistic, but eye catching and should speak to high level executives. Our primary focus areas consist of executive assistance and government contracting.

Target Market(s)

CEOs and executives

Contact Information for Business Card

see project description. phone, email, website.

Colors

Designer to choose only greyscale colors for use in the design.

```html
<!DOCTYPE html>
<html lang="en">
<head>
<meta charset="utf-8">
<title>RKP Advisory — Business Card</title>
<link rel="stylesheet" href="https://fonts.googleapis.com/css2?family=EB+Garamond:wght@500;700&family=Montserrat:wght@400&display=swap">
<style>
  :root {
    --page-bg: #d9d9d9;
    --card-bg: #1e1e1e;
    --ink-light: #ffffff;
    --ink-soft: #e6e6e6;
    --ink-mark: #474747;
    --card-shadow: rgba(0, 0, 0, 0.35);
  }
  * { margin: 0; padding: 0; box-sizing: border-box; }
  html, body {
    width: 900px;
    height: 1200px;
    overflow: hidden;
    background: var(--page-bg);
  }
  .canvas {
    position: relative;
    width: 900px;
    height: 1200px;
  }
  .card {
    position: absolute;
    background: var(--card-bg);
    border-radius: 24px;
    box-shadow: 0 6px 16px var(--card-shadow);
    overflow: hidden;
  }
  .card--front { left: 80px; top: 130px; width: 742px; height: 442px; }
  .card--back  { left: 78px; top: 638px; width: 744px; height: 440px; }

  .company-name {
    position: absolute;
    left: 31px;
    top: 32px;
    font-family: "EB Garamond", serif;
    font-weight: 500;
    font-size: 50px;
    line-height: 1;
    color: var(--ink-light);
  }
  .front-mark {
    position: absolute;
    right: 36px;
    top: 170px;
    font-family: "EB Garamond", serif;
    font-weight: 500;
    font-size: 60px;
    line-height: 1;
    color: var(--ink-mark);
  }
  .person { position: absolute; left: 42px; top: 202px; }
  .person__name {
    font-family: "EB Garamond", serif;
    font-weight: 700;
    font-size: 27px;
    line-height: 1.1;
    color: var(--ink-light);
  }
  .person__role {
    font-family: "Montserrat", sans-serif;
    font-size: 16px;
    color: var(--ink-soft);
    margin-top: 2px;
  }
  .contact-list {
    position: absolute;
    left: 42px;
    top: 290px;
    list-style: none;
  }
  .contact-list__item {
    display: flex;
    align-items: center;
    gap: 8px;
    height: 28px;
    font-family: "Montserrat", sans-serif;
    font-size: 16.5px;
    color: var(--ink-soft);
  }
  .contact-list__icon { width: 17px; height: 17px; fill: var(--ink-light); }
  .tagline {
    position: absolute;
    left: 42px;
    top: 390px;
    font-family: "EB Garamond", serif;
    font-weight: 500;
    font-size: 17px;
    letter-spacing: 0.3px;
    color: var(--ink-soft);
  }
  .back-mark {
    position: absolute;
    left: 0;
    right: 0;
    top: 180px;
    text-align: center;
    font-family: "EB Garamond", serif;
    font-weight: 500;
    font-size: 74px;
    line-height: 1;
    color: var(--ink-light);
  }
</style>
</head>
<body>
<main class="canvas">
  <section class="card card--front" aria-label="Card front">
    <h1 class="company-name">RKP Advisory</h1>
    <div class="front-mark" aria-hidden="true">RKP Advisory</div>

    <div class="person">
      <p class="person__name">Melissa Thornbury</p>
      <p class="person__role">Owner/CEO</p>
    </div>

    <ul class="contact-list">
      <li class="contact-list__item">
        <svg class="contact-list__icon" viewBox="0 0 24 24" aria-hidden="true"><path d="M6.6 10.8a15.1 15.1 0 0 0 6.6 6.6l2.2-2.2a1 1 0 0 1 1-.25 11.4 11.4 0 0 0 3.6.57 1 1 0 0 1 1 1V20a1 1 0 0 1-1 1A17 17 0 0 1 3 4a1 1 0 0 1 1-1h3.5a1 1 0 0 1 1 1c0 1.25.2 2.45.57 3.57a1 1 0 0 1-.25 1z"/></svg>
        555.302.9817
      </li>
      <li class="contact-list__item">
        <svg class="contact-list__icon" viewBox="0 0 24 24" aria-hidden="true"><path d="M3 6h18v1.2l-9 5.6-9-5.6zM3 9.5l9 5.6 9-5.6V18H3z"/></svg>
        info@rkpadvisory.net
      </li>
      <li class="contact-list__item">
        <svg class="contact-list__icon" viewBox="0 0 24 24" aria-hidden="true"><path d="M12 2a10 10 0 1 0 0 20 10 10 0 0 0 0-20zm-1 17.9A8 8 0 0 1 4.1 10L9 15v1a2 2 0 0 0 2 2zm6.9-2.5A2 2 0 0 0 16 16h-1v-3a1 1 0 0 0-1-1H8v-2h2a1 1 0 0 0 1-1V7h2a2 2 0 0 0 2-2v-.4a8 8 0 0 1 2.9 12.8z"/></svg>
        www.rkpadvisory.net
      </li>
    </ul>

    <p class="tagline">VIRTUAL ASSISTANCE</p>
  </section>

  <section class="card card--back" aria-label="Card back">
    <div class="back-mark">RKP Advisory</div>
  </section>
</main>
</body>
</html>
```